Modern Business Card For A Digital Advertising Company

I'll be print on the Pell Prints Velour paper http://us.pellprints.com/products/velour/business-cards.html
Need's to be modern and use the color palette of the logo or gray scales. I think integrating the pixelation of the logo in to the card and having it wrap from one side to the other could be interesting. My company provides ad operations, web development, and number of other services to websites around the world. You can see my website at http://www.zantorhq.com
Contact info on the card needs to have
Owen Lasko
President
p.318.204.6637
owen@zantorhq.com
http://www.zantorhq.com
Doesn't necessarily need to be in that order
Website owners
Business

```html
<!DOCTYPE html>
<html lang="en">
<head>
<meta charset="utf-8">
<title>Zantor HQ — Business Card</title>
<link href="https://fonts.googleapis.com/css2?family=Open+Sans:wght@700&family=Tinos:wght@400;700&display=swap" rel="stylesheet">
<style>
  :root {
    --stage: #232323;
    --paper: #ffffff;
    --green-deep: #5a962b;
    --green-bright: #8cc63f;
    --ink-dark: #3a3a3a;
    --text-light: #ffffff;
  }
  * { margin: 0; padding: 0; box-sizing: border-box; }
  html, body {
    width: 1200px; height: 763px; overflow: hidden;
    background: var(--stage);
  }
  .stage {
    position: relative; width: 1200px; height: 763px;
    display: flex; align-items: center; justify-content: center; gap: 40px;
  }
  .card {
    position: relative; width: 520px; height: 297px; overflow: hidden;
    box-shadow: 0 10px 30px rgba(0,0,0,.5);
  }

  /* Front */
  .card--front { background: var(--paper); }
  .card__wave { position: absolute; inset: 0; width: 100%; height: 100%; }
  .brand {
    position: absolute; top: 62px; left: 0; right: 0;
    display: flex; align-items: center; justify-content: center; gap: 12px;
    font-family: 'Open Sans', sans-serif; font-weight: 700;
    font-size: 40px; color: var(--green-bright); letter-spacing: 1px;
  }
  .brand__square { width: 30px; height: 30px; background: var(--green-bright); }
  .contact {
    position: absolute; left: 0; right: 0; top: 196px;
    text-align: center; color: var(--text-light);
    font-family: 'Tinos', serif;
  }
  .contact__name { font-size: 21px; font-weight: 700; }
  .contact__title { font-size: 16px; font-weight: 400; }
  .contact__row {
    display: flex; justify-content: center; align-items: center; gap: 14px;
    font-size: 15px; margin-top: 6px;
  }
  .contact__item { display: inline-flex; align-items: center; gap: 5px; }
  .icon { width: 12px; height: 12px; fill: var(--text-light); }

  /* Back */
  .card--back {
    background: linear-gradient(160deg, var(--green-deep) 0%, var(--green-bright) 100%);
  }
  .card--back .brand {
    top: 100px; color: var(--paper); font-size: 52px;
  }
  .card--back .brand__square { width: 38px; height: 38px; background: var(--paper); }
  .back__url {
    position: absolute; left: 0; right: 0; bottom: 34px; text-align: center;
    font-family: 'Open Sans', sans-serif; font-weight: 700;
    font-size: 18px; color: var(--text-light); letter-spacing: .5px;
  }
</style>
</head>
<body>
<main class="stage">
  <section class="card card--front" aria-label="Card front">
    <svg class="card__wave" viewBox="0 0 520 297" preserveAspectRatio="none" aria-hidden="true">
      <defs>
        <linearGradient id="bandGreen" x1="0" y1="1" x2="1" y2="0">
          <stop offset="0" stop-color="#5a962b"/>
          <stop offset="1" stop-color="#8cc63f"/>
        </linearGradient>
      </defs>
      <path d="M0,262 Q250,150 520,140 L520,297 L0,297 Z" fill="url(#bandGreen)"/>
      <path d="M0,256 Q240,140 520,128 Q240,134 0,246 Z" fill="#3a3a3a"/>
    </svg>
    <div class="brand"><span class="brand__square"></span>Zantor HQ</div>
    <div class="contact">
      <p><span class="contact__name">Owen Lasko,</span> <span class="contact__title">President</span></p>
      <p class="contact__row">
        <span class="contact__item">
          <svg class="icon" viewBox="0 0 24 24"><path d="M6.6 10.8a15 15 0 0 0 6.6 6.6l2.2-2.2c.3-.3.7-.4 1-.2 1.1.4 2.3.6 3.6.6.6 0 1 .4 1 1V20c0 .6-.4 1-1 1A17 17 0 0 1 3 4c0-.6.4-1 1-1h3.5c.6 0 1 .4 1 1 0 1.3.2 2.5.6 3.6.1.3 0 .7-.2 1z"/></svg>318.204.6637
        </span>
        <span class="contact__item">
          <svg class="icon" viewBox="0 0 24 24"><path d="M2 5h20v14H2zm2 2v.5l8 5 8-5V7z"/></svg>owen@zantorhq.com
        </span>
      </p>
      <p class="contact__row">
        <span class="contact__item">
          <svg class="icon" viewBox="0 0 24 24"><circle cx="12" cy="12" r="10"/></svg>www.zantorhq.com
        </span>
      </p>
    </div>
  </section>

  <section class="card card--back" aria-label="Card back">
    <div class="brand"><span class="brand__square"></span>Zantor HQ</div>
    <p class="back__url">www.zantorhq.com</p>
  </section>
</main>
</body>
</html>
```